TALMORK

The business want a professional looking business card. We have a scetch we will add but want the extra upgrade, and would like more suggestions for variations of our business cards.

```html
<!DOCTYPE html>
<html lang="en">
<head>
<meta charset="UTF-8">
<title>TALMORK — Business Card</title>
<link href="https://fonts.googleapis.com/css2?family=Cinzel:wght@500&family=Libre+Baskerville:wght@700&family=Poppins:wght@400&display=swap" rel="stylesheet">
<style>
  :root {
    --page-bg: #efefef;
    --green-deep: #0c2a22;
    --green-mid: #08201a;
    --black: #020404;
    --gold: #c9a24a;
    --gold-light: #e6c878;
    --gold-dark: #9a7a30;
    --line-gold: #8f7a3e;
    --ink: #1a1a1a;
    --white: #ffffff;
  }
  * { margin: 0; padding: 0; box-sizing: border-box; }
  html, body { width: 1200px; height: 2245px; overflow: hidden; background: var(--page-bg); }
  .canvas { position: relative; width: 1200px; height: 2245px; }

  .card {
    position: absolute; left: 121px; width: 959px; height: 548px; overflow: hidden;
    box-shadow: 18px 22px 28px rgba(0,0,0,0.28);
  }
  .card--front { top: 520px;
    background:
      radial-gradient(ellipse 70% 90% at 35% 45%, #12332a 0%, var(--green-mid) 55%, var(--black) 100%);
  }
  .card--back { top: 1178px; background: var(--white); }

  .sweep { position: absolute; inset: 0; pointer-events: none; }

  .frame { position: absolute; left: 49px; top: 49px; right: 50px; bottom: 52px; border: 1px solid var(--line-gold); }

  .flourish {
    position: absolute; width: 90px; height: 100px;
    background: linear-gradient(135deg, rgba(230,200,120,0.55), rgba(154,122,48,0.15));
    border-radius: 2px;
  }
  .flourish--tl { left: 42px; top: 42px; }
  .flourish--tr { right: 42px; top: 42px; }
  .flourish--bl { left: 42px; bottom: 44px; }
  .flourish--br { right: 42px; bottom: 44px; }

  .brand { position: absolute; text-align: center; color: var(--gold); font-family: "Cinzel", serif; }
  .brand__dot { display: block; margin: 0 auto; border-radius: 50%; background: var(--gold); }
  .brand__name { font-weight: 500; letter-spacing: 0.28em; line-height: 1; }
  .brand__since { font-family: "Poppins", sans-serif; letter-spacing: 0.42em; line-height: 1; margin-top: 12px; }

  .card--front .brand { left: 0; width: 959px; top: 200px; }
  .card--front .brand__dot { width: 64px; height: 64px; margin-bottom: 62px; }
  .card--front .brand__name { font-size: 40px; padding-left: 0.28em; }
  .card--front .brand__since { font-size: 14px; padding-left: 0.42em; }

  .panel {
    position: absolute; left: 0; top: 0; width: 422px; height: 548px; overflow: hidden;
    background: radial-gradient(ellipse 90% 80% at 55% 55%, #0f2f27 0%, var(--green-mid) 55%, var(--black) 100%);
  }
  .card--back .brand { left: 0; width: 422px; top: 212px; }
  .card--back .brand__dot { width: 54px; height: 54px; margin-bottom: 46px; }
  .card--back .brand__name { font-size: 34px; padding-left: 0.28em; }
  .card--back .brand__since { font-size: 12px; padding-left: 0.42em; margin-top: 10px; }

  .details { position: absolute; left: 474px; top: 150px; }
  .details__name { font-family: "Libre Baskerville", serif; font-weight: 700; font-size: 31px; line-height: 1;
    color: var(--gold); letter-spacing: -0.01em; }
  .details__role { font-family: "Poppins", sans-serif; font-size: 19px; color: var(--gold-dark); margin-top: 8px; line-height: 1.2; }
  .details__rule { width: 87px; height: 1px; background: var(--line-gold); margin: 22px 0 40px 1px; }
  .contact { list-style: none; }
  .contact__item { display: flex; align-items: center; height: 40px;
    font-family: "Poppins", sans-serif; font-size: 24px; color: var(--ink); }
  .contact__icon { width: 20px; height: 20px; margin-right: 13px; margin-left: 4px; flex: none; }
</style>
</head>
<body>
<div class="canvas">

  <section class="card card--front">
    <svg class="sweep" width="959" height="548" viewBox="0 0 959 548" aria-hidden="true">
      <path d="M560 548 C 760 420 880 250 930 0 L 959 0 L 959 548 Z" fill="rgba(0,0,0,0.35)"/>
      <path d="M0 420 C 260 380 520 260 700 0 L 760 0 C 560 300 300 430 0 470 Z" fill="rgba(255,255,255,0.02)"/>
    </svg>
    <div class="frame"></div>
    <div class="flourish flourish--tl" role="img" aria-label="Gold corner flourish"></div>
    <div class="flourish flourish--tr" role="img" aria-label="Gold corner flourish"></div>
    <div class="flourish flourish--bl" role="img" aria-label="Gold corner flourish"></div>
    <div class="flourish flourish--br" role="img" aria-label="Gold corner flourish"></div>
    <div class="brand">
      <span class="brand__dot"></span>
      <div class="brand__name">TALMORK</div>
      <div class="brand__since">SINCE 2026</div>
    </div>
  </section>

  <section class="card card--back">
    <div class="panel">
      <svg class="sweep" width="422" height="548" viewBox="0 0 422 548" aria-hidden="true">
        <path d="M60 0 C 140 140 280 260 422 300 L 422 0 Z" fill="rgba(255,255,255,0.03)"/>
      </svg>
    </div>
    <div class="frame"></div>
    <div class="flourish flourish--tl" role="img" aria-label="Gold corner flourish"></div>
    <div class="flourish flourish--tr" role="img" aria-label="Gold corner flourish"></div>
    <div class="flourish flourish--bl" role="img" aria-label="Gold corner flourish"></div>
    <div class="flourish flourish--br" role="img" aria-label="Gold corner flourish"></div>
    <div class="brand">
      <span class="brand__dot"></span>
      <div class="brand__name">TALMORK</div>
      <div class="brand__since">SINCE 2026</div>
    </div>

    <div class="details">
      <h1 class="details__name">Lars Henrik Solvang</h1>
      <p class="details__role">CEO &amp; Founder</p>
      <div class="details__rule"></div>
      <ul class="contact">
        <li class="contact__item">
          <svg class="contact__icon" viewBox="0 0 20 20" aria-hidden="true"><rect x="5" y="1" width="10" height="18" rx="2" fill="none" stroke="#b8913c" stroke-width="1.6"/><line x1="8.5" y1="16" x2="11.5" y2="16" stroke="#b8913c" stroke-width="1.4"/></svg>
          004791234567
        </li>
        <li class="contact__item">
          <svg class="contact__icon" viewBox="0 0 20 20" aria-hidden="true"><rect x="1" y="5" width="18" height="11" fill="#c9a24a"/><path d="M1 5 L10 12 L19 5" fill="none" stroke="#f3e2b0" stroke-width="1.2"/></svg>
          talmork.llc@mailhub.com
        </li>
        <li class="contact__item">
          <svg class="contact__icon" viewBox="0 0 20 20" aria-hidden="true"><circle cx="10" cy="10" r="8.5" fill="none" stroke="#b8913c" stroke-width="1.6"/><ellipse cx="10" cy="10" rx="3.6" ry="8.5" fill="none" stroke="#b8913c" stroke-width="1.3"/><line x1="1.5" y1="10" x2="18.5" y2="10" stroke="#b8913c" stroke-width="1.3"/></svg>
          www.talmork.llc
        </li>
      </ul>
    </div>
  </section>

</div>
</body>
</html>
```